Awesome photographers card for an awesome new business

Double sided business card Black background and silver logo in middle on one side. Details on otherside. please keep it simple

Industry/Entity Type

Photographer

Contact Information for Business Card

Gerald Fenwick
0452817360
GeraldFenwickPhotography47@mailbox.test
www.GeraldFenwickPhotography.test.au
Instagram _Gerald_fenwick

Requirements
Must have
• My logo in Silver
• please use instagram logo instead of "Instagram"

```html
<!DOCTYPE html>
<html lang="en">
<head>
<meta charset="utf-8">
<title>Gerald Fenwick Photography – Business Card</title>
<link rel="stylesheet" href="https://fonts.googleapis.com/css2?family=Roboto:wght@400;500;700&display=swap">
<style>
  :root {
    --stage: #2b2b2c;
    --card-dark: #1b1c1e;
    --card-dark-top: #232426;
    --silver-light: #e6e6e8;
    --silver-mid: #bdbdc0;
    --silver-deep: #9a9a9e;
    --ink: #111213;
    --text-light: #e4e4e4;
    --icon-grey: #9a9a9a;
  }
  * { margin: 0; padding: 0; box-sizing: border-box; }
  html, body { width: 1200px; height: 960px; overflow: hidden; }
  body {
    background: var(--stage);
    font-family: "Roboto", Arial, sans-serif;
    position: relative;
  }
  .card {
    position: absolute;
    width: 600px;
    height: 342px;
    overflow: hidden;
  }
  .card--front {
    left: 314px; top: 113px;
    background: linear-gradient(180deg, var(--card-dark-top), var(--card-dark));
  }
  .card--back {
    left: 311px; top: 472px;
    background: linear-gradient(90deg, var(--silver-deep) 0%, var(--silver-light) 30%, var(--silver-mid) 55%, var(--silver-light) 78%, var(--silver-deep) 100%);
  }
  .brand-mark {
    position: absolute;
    left: 50%;
    transform: translateX(-50%);
    border-radius: 50%;
    display: flex;
    align-items: center;
    justify-content: center;
    text-align: center;
    font-weight: 500;
    line-height: 1.2;
    letter-spacing: 1px;
  }
  .card--front .brand-mark {
    top: 52px; width: 140px; height: 140px;
    border: 3px solid var(--silver-mid);
    color: var(--silver-mid);
    font-size: 17px;
  }
  .card--back .brand-mark {
    top: 93px; width: 170px; height: 170px;
    border: 3px solid var(--ink);
    color: var(--ink);
    font-size: 20px;
  }
  .holder-name {
    position: absolute;
    top: 212px; width: 100%;
    text-align: center;
    font-size: 20px;
    font-weight: 700;
    color: var(--silver-mid);
    letter-spacing: 0.5px;
  }
  .contact-line {
    position: absolute;
    width: 100%;
    display: flex;
    justify-content: center;
    align-items: center;
    gap: 6px;
    font-size: 14px;
    color: var(--text-light);
  }
  .contact-line--main { top: 246px; }
  .contact-line--social { top: 265px; }
  .contact-line svg { flex: none; }
  .contact-gap { width: 4px; }
  .silver-band {
    position: absolute;
    left: 0; top: 270px;
    width: 600px; height: 72px;
  }
  .web-address {
    position: absolute;
    width: 100%;
    text-align: center;
    color: var(--ink);
  }
  .card--front .web-address { top: 318px; font-size: 14px; }
  .card--back .web-address { top: 291px; font-size: 15px; letter-spacing: 2px; }
</style>
</head>
<body>
  <section class="card card--front">
    <div class="brand-mark">Gerald<br>Fenwick</div>
    <div class="holder-name">GERALD FENWICK</div>
    <div class="contact-line contact-line--main">
      <svg width="12" height="12" viewBox="0 0 24 24" aria-hidden="true"><path fill="var(--icon-grey)" d="M6.6 10.8a15.1 15.1 0 0 0 6.6 6.6l2.2-2.2a1 1 0 0 1 1-.25 11.4 11.4 0 0 0 3.6.57 1 1 0 0 1 1 1V20a1 1 0 0 1-1 1A17 17 0 0 1 3 4a1 1 0 0 1 1-1h3.5a1 1 0 0 1 1 1c0 1.25.2 2.45.57 3.6a1 1 0 0 1-.25 1z"/></svg>
      <span>0452817360</span>
      <span class="contact-gap"></span>
      <svg width="13" height="10" viewBox="0 0 26 20" aria-hidden="true"><rect width="26" height="20" rx="2" fill="var(--icon-grey)"/><path d="M1 2l12 9 12-9" fill="none" stroke="var(--card-dark)" stroke-width="2"/></svg>
      <span>GeraldFenwickPhotography47@mailbox.test</span>
    </div>
    <div class="contact-line contact-line--social">
      <svg width="14" height="14" viewBox="0 0 14 14" aria-hidden="true"><rect width="14" height="14" rx="2" fill="var(--icon-grey)"/></svg>
      <span>Gerald_fenwick</span>
    </div>
    <svg class="silver-band" viewBox="0 0 600 72" aria-hidden="true">
      <defs>
        <linearGradient id="band-fill" x1="0" x2="1" y1="0" y2="0">
          <stop offset="0" stop-color="#a9a9ac"/>
          <stop offset="0.35" stop-color="#e2e2e4"/>
          <stop offset="0.65" stop-color="#c4c4c7"/>
          <stop offset="1" stop-color="#a4a4a8"/>
        </linearGradient>
      </defs>
      <path d="M0 8 Q300 34 600 8 L600 72 L0 72 Z" fill="url(#band-fill)"/>
      <path d="M60 18 Q300 36 540 14" fill="none" stroke="#0c0c0d" stroke-width="3"/>
    </svg>
    <div class="web-address">www.GeraldFenwickPhotography.test.au</div>
  </section>

  <section class="card card--back">
    <div class="brand-mark">Gerald<br>Fenwick</div>
    <div class="web-address">www.GeraldFenwickPhotography.test.au</div>
  </section>
</body>
</html>
```